SaaS Early tech startup business card design

Unique design for experience ecommerce platform company. the business cards will be used by executive members. conformance with color code is required.

```html
<!DOCTYPE html>
<html lang="en">
<head>
<meta charset="utf-8">
<title>Kovra Business Card</title>
<link rel="stylesheet" href="https://fonts.googleapis.com/css2?family=Lato:wght@400;700&family=Montserrat:wght@700;800&display=swap">
<style>
  :root {
    --stage: #2a2a2a;
    --deep-blue: #0a6590;
    --teal: #00b09a;
    --teal-soft: #3dbfa3;
    --teal-dark: #00a190;
    --arc-blue: #0f6f98;
    --mark-teal: #1d9bab;
    --paper: #ffffff;
  }
  * { box-sizing: border-box; margin: 0; padding: 0; }
  html, body { width: 1200px; height: 1015px; overflow: hidden; }
  body {
    background: var(--stage);
    display: flex;
    flex-direction: column;
    align-items: center;
    justify-content: center;
    gap: 50px;
    font-family: "Lato", sans-serif;
  }
  .card {
    position: relative;
    width: 700px;
    height: 400px;
    overflow: hidden;
    box-shadow: 0 14px 30px rgba(0,0,0,0.45);
  }
  .card-back {
    background: linear-gradient(170deg, var(--deep-blue) 0%, var(--teal) 65%, var(--teal) 100%);
    display: flex;
    align-items: center;
    justify-content: center;
  }
  .brand-name {
    font-family: "Montserrat", sans-serif;
    font-weight: 800;
    letter-spacing: 1px;
    text-transform: lowercase;
    line-height: 1;
  }
  .card-back .brand-name { font-size: 110px; color: var(--mark-teal); }
  .card-front .front-bg { position: absolute; inset: 0; }
  .front-brand {
    position: absolute;
    left: 430px; top: 95px;
    width: 270px;
    text-align: center;
  }
  .card-front .brand-name { font-size: 84px; color: var(--mark-teal); }
  .person {
    position: absolute;
    left: 62px; top: 120px;
    color: var(--paper);
  }
  .person-name {
    font-family: "Montserrat", sans-serif;
    font-weight: 700;
    font-size: 24px;
    text-transform: uppercase;
    letter-spacing: 0.5px;
  }
  .person-title { font-size: 19px; margin-top: 1px; }
  .address {
    position: absolute;
    left: 62px; top: 228px;
    color: var(--paper);
    font-size: 19px;
    line-height: 1.2;
  }
  .contacts {
    position: absolute;
    left: 62px; top: 292px;
    list-style: none;
    color: var(--paper);
    font-size: 19px;
    line-height: 1.3;
  }
  .contacts li { display: flex; align-items: center; gap: 8px; }
  .contacts svg { width: 17px; height: 17px; flex: none; }
</style>
</head>
<body>
  <section class="card card-back" aria-label="Card back">
    <span class="brand-name">kovra</span>
  </section>

  <section class="card card-front" aria-label="Card front">
    <svg class="front-bg" viewBox="0 0 700 400" preserveAspectRatio="none" aria-hidden="true">
      <defs>
        <linearGradient id="frontTeal" x1="0" y1="0" x2="0" y2="1">
          <stop offset="0" stop-color="#3dbfa3"/>
          <stop offset="1" stop-color="#00a190"/>
        </linearGradient>
      </defs>
      <rect width="700" height="400" fill="url(#frontTeal)"/>
      <path d="M430 0 H700 V400 H480 C420 370 385 300 385 190 C385 100 400 40 430 0 Z" fill="#ffffff"/>
      <path d="M455 18 C405 70 390 140 395 210 C402 300 445 355 500 380" fill="none" stroke="var(--arc-blue)" stroke-width="4" stroke-linecap="round"/>
    </svg>

    <div class="front-brand"><span class="brand-name">kovra</span></div>

    <div class="person">
      <p class="person-name">Daniel Reyes</p>
      <p class="person-title">Managing Director</p>
    </div>

    <address class="address" style="font-style:normal">
      87, Harbor Lane Suite 4<br>
      Portland, OR 97209
    </address>

    <ul class="contacts">
      <li>
        <svg viewBox="0 0 24 24" aria-hidden="true"><path fill="#fff" d="M6.6 10.8c1.4 2.8 3.8 5.1 6.6 6.6l2.2-2.2c.3-.3.7-.4 1-.2 1.1.4 2.3.6 3.6.6.6 0 1 .4 1 1V20c0 .6-.4 1-1 1C10.6 21 3 13.4 3 4c0-.6.4-1 1-1h3.5c.6 0 1 .4 1 1 0 1.3.2 2.5.6 3.6.1.3 0 .7-.2 1z"/></svg>
        055-214 378 960
      </li>
      <li>
        <svg viewBox="0 0 24 24" aria-hidden="true"><path fill="#fff" d="M2 5h20v14H2z M4 7v.4l8 5.2 8-5.2V7z" fill-rule="evenodd"/></svg>
        hello@kovra.io
      </li>
      <li>
        <svg viewBox="0 0 24 24" aria-hidden="true"><g fill="none" stroke="#fff" stroke-width="2"><circle cx="12" cy="12" r="9"/><path d="M3 12h18M12 3c3 3 3 15 0 18M12 3c-3 3-3 15 0 18"/></g></svg>
        www.kovra.io
      </li>
    </ul>
  </section>
</body>
</html>
```